We’re a real estate firm that has landed a big builder in a neighboring state. Our branding needs...

We are a real estate firm who represents various builders along with doing resale here in Oregon. Our firm is growing to represent a big builder in Washington State and we’ll have another 40 brokers on our team. We need rebranding. As in, a new logo ( the house logo we have now looks cartoonish, hate it). We need new cards, something to really stand out. I’ve been thinking of using those NFC cards from ZEP or the ones with the seam color. I likely want two or three designs, a darker (as in a background color of black or grey) , a light one ( again I mean background color) and a credit card style (either plastic w an embossed name/number on front, or metal ). I’m thinking dark background for cc, or silver if it’s metal. That’s my thoughts, but you are the artists, so maybe you have an idea I haven’t considered. Our colors were black and red, but we don’t have to stick to that. Just nothing too busy. Oh, and we are typically representing the local, higher quality builders in our area (just below custom), but not national. Subdivisions are near the Kell Varney, Brisco, and Thornfield Crest sites. We are super excited, but without a lot of time to change the “look” of our brokerage. So I’ll be deciding and moving forward within 24 hours tops. Our name is Real Estate Summit Alliance ( we cant change the name because of timeline and business license) Thank you!

Industry/Entity Type

Real Estate

Contact Information for Business Card

The usual. Name of firm. Name of cardholder. Contact info.

Font styles to use
Serif
Sans Serif

Colors

Designer to choose colors to be used in the design.

Requirements
Must have
• A sleek or simple look. I included photos of cards with stylistic attributes we like. Thank you
Nice to have
• We really like the black backgrounds. With foil or embossed detail. We also like the black on black. Matte black card with raised shiny black detail. But still eye catching.
Should not have
• No ornate or busy looking style. We don’t want anything cluttered.

```html
<!DOCTYPE html>
<html lang="en">
<head>
<meta charset="utf-8">
<title>Real Estate Summit Alliance – Business Cards</title>
<link rel="stylesheet" href="https://fonts.googleapis.com/css2?family=Open+Sans:wght@400;600;700&display=swap">
<style>
  :root {
    --backdrop: #dadada;
    --card-light: #ffffff;
    --card-dark: #0f3063;
    --ink: #2b2b2b;
    --on-dark: #ffffff;
    --rule-dark: rgba(255,255,255,0.75);
  }
  * { box-sizing: border-box; margin: 0; padding: 0; }
  html, body {
    width: 1200px; height: 900px; overflow: hidden;
    background: var(--backdrop);
    font-family: "Open Sans", sans-serif;
  }
  .stage { position: relative; width: 1200px; height: 900px; }
  .card {
    position: absolute;
    width: 560px; height: 320px;
    border-radius: 30px;
    box-shadow: 0 14px 30px rgba(0,0,0,0.18);
  }
  .firm-name {
    font-family: "Open Sans", sans-serif;
    font-weight: 600;
    white-space: nowrap;
    text-align: center;
  }
  /* Front: light card with firm name and address */
  .card--front {
    left: 70px; top: 120px;
    background: var(--card-light);
    color: var(--ink);
    display: flex; flex-direction: column; align-items: center; justify-content: center;
  }
  .card--front .firm-name { font-size: 26px; }
  .address {
    margin-top: 40px;
    font-size: 15px;
    letter-spacing: 0.6px;
  }
  /* Back: dark card with cardholder details */
  .card--back {
    left: 570px; top: 470px;
    background: var(--card-dark);
    color: var(--on-dark);
    padding: 48px 56px;
    display: flex; flex-direction: column; align-items: center;
  }
  .card--back .firm-name { font-size: 28px; }
  .rule { width: 300px; height: 1px; background: var(--rule-dark); margin: 16px 0; }
  .holder__name { font-weight: 700; font-size: 19px; letter-spacing: 1px; }
  .holder__title { font-size: 14px; margin-top: 2px; }
  .contact { font-size: 14px; text-align: center; line-height: 1.6; }
  .contact b { font-weight: 700; }
</style>
</head>
<body>
<main class="stage">
  <section class="card card--front" aria-label="Card front">
    <p class="firm-name">Real Estate Summit Alliance</p>
    <p class="address">4820 Alder Ridge Lane, Portland, OR 97205.</p>
  </section>

  <section class="card card--back" aria-label="Card back">
    <p class="firm-name">Real Estate Summit Alliance</p>
    <div class="rule"></div>
    <div class="holder__name">MARCUS HALE</div>
    <div class="holder__title">Managing Director</div>
    <div class="rule"></div>
    <div class="contact">
      <div><b>P:</b> 503-555 0148 | <b>M:</b> 503-555 0173</div>
      <div><b>E:</b> hello@summitalliance.co | <b>W:</b> www.summitalliance.co</div>
    </div>
  </section>
</main>
</body>
</html>
```